FREE Network Assessment image for landing page

This graphic will be on a landing page and on the left will be Text and a download button that we change and control. The graphic for this project will be to the right.
I will add an example of the landing page area so that it makes more sense.

Please include the text from the sample - the font needs to be the same style as what we are using on the left side!

The graphic needs to be a .png file, roughly 713 x 527 white background. Use discretion on design layout.

Colors are black, Red = PMS 1795 and Gray = Cool Gray 10

Thanks,
Tom Garrick

Target Market(s)

small businesses

Industry/Entity Type

Information Technology

Font styles to use
Other font styles liked:
• See sample

Requirements
Must have
• see description
Nice to have
• Possibly small technology related image to help enhance the text but I don't want any image to compete with the text. Keep in mind the colors mentioned in the description - this is the web site colors.
Should not have
• Should not be hard to read

```html
<!DOCTYPE html>
<html lang="en">
<head>
<meta charset="UTF-8">
<title>Free Network &amp; Computer Health Check Service</title>
<link rel="stylesheet" href="https://fonts.googleapis.com/css2?family=Oswald:wght@300;500;600&family=Arimo:wght@400&display=swap">
<style>
  :root {
    --frame-grey: #5d595a;
    --panel-white: #ffffff;
    --brand-red: #e0282f;
    --brand-red-dark: #b81d24;
    --cool-grey: #58585a;
    --body-text: #3a3a3c;
    --button-shadow: #6a6668;
  }
  * { margin: 0; padding: 0; box-sizing: border-box; }
  html, body {
    width: 1200px;
    height: 886px;
    overflow: hidden;
    background: var(--frame-grey);
  }
  .canvas {
    position: relative;
    width: 1200px;
    height: 886px;
    background: var(--frame-grey);
  }
  .panel {
    position: absolute;
    left: 42px;
    top: 31px;
    width: 1116px;
    height: 824px;
    background: var(--panel-white);
  }
  .headline {
    position: absolute;
    left: 30px;
    top: 42px;
    font-family: "Oswald", sans-serif;
    text-transform: uppercase;
    line-height: 1;
  }
  .headline-line {
    display: block;
    white-space: nowrap;
  }
  .headline-top {
    font-size: 92px;
    font-weight: 300;
    color: var(--cool-grey);
    letter-spacing: -0.5px;
    transform: scaleX(0.9);
    transform-origin: left center;
  }
  .headline-bottom {
    font-size: 104px;
    font-weight: 600;
    color: var(--cool-grey);
    margin-top: -2px;
    transform: scaleX(0.86);
    transform-origin: left center;
  }
  .accent { color: var(--brand-red); font-weight: 600; }

  .benefits {
    position: absolute;
    left: 52px;
    top: 270px;
    width: 790px;
    list-style: none;
    font-family: "Arimo", Arial, sans-serif;
    font-size: 26.5px;
    line-height: 37px;
    color: var(--body-text);
  }
  .benefit {
    position: relative;
    padding-left: 37px;
    margin-bottom: 14px;
  }
  .benefit-tick {
    position: absolute;
    left: 0;
    top: 11px;
    width: 20px;
    height: 18px;
  }

  .device-visual {
    position: absolute;
    left: 836px;
    top: 267px;
    width: 276px;
    height: 276px;
    background: radial-gradient(circle at 45% 48%, #ffffff 0%, #f1f1f1 35%, #d8d8d8 60%, rgba(255,255,255,0) 78%);
  }

  .cta-button {
    position: absolute;
    left: 33px;
    top: 659px;
    width: 280px;
    height: 118px;
    border-radius: 12px;
    background: var(--brand-red);
    box-shadow: 9px 9px 0 var(--button-shadow);
    font-family: "Oswald", sans-serif;
    text-transform: uppercase;
    color: var(--panel-white);
    text-align: center;
    text-decoration: none;
    display: flex;
    flex-direction: column;
    justify-content: center;
    line-height: 1;
  }
  .cta-main {
    font-size: 68px;
    font-weight: 500;
    transform: scaleX(0.85);
  }
  .cta-sub {
    font-size: 34px;
    font-weight: 500;
    margin-top: 2px;
    transform: scaleX(0.82);
  }
</style>
</head>
<body>
<div class="canvas">
  <section class="panel">
    <h1 class="headline">
      <span class="headline-line headline-top"><span class="accent">Free</span> Network &amp; Computer</span>
      <span class="headline-line headline-bottom">Health Check <span class="accent">Service</span></span>
    </h1>

    <ul class="benefits">
      <li class="benefit">
        <svg class="benefit-tick" viewBox="0 0 20 18" aria-hidden="true"><path d="M2 10 L8 15 L18 2" fill="none" stroke="#e0282f" stroke-width="3" stroke-linecap="round" stroke-linejoin="round"/></svg>
        Check your network’s security against hacker attacks, theft, ransomware, viruses, and more.
      </li>
      <li class="benefit">
        <svg class="benefit-tick" viewBox="0 0 20 18" aria-hidden="true"><path d="M2 10 L8 15 L18 2" fill="none" stroke="#e0282f" stroke-width="3" stroke-linecap="round" stroke-linejoin="round"/></svg>
        See who and what has access to your network and data.
      </li>
      <li class="benefit">
        <svg class="benefit-tick" viewBox="0 0 20 18" aria-hidden="true"><path d="M2 10 L8 15 L18 2" fill="none" stroke="#e0282f" stroke-width="3" stroke-linecap="round" stroke-linejoin="round"/></svg>
        Perform network and Internet speed test
      </li>
      <li class="benefit">
        <svg class="benefit-tick" viewBox="0 0 20 18" aria-hidden="true"><path d="M2 10 L8 15 L18 2" fill="none" stroke="#e0282f" stroke-width="3" stroke-linecap="round" stroke-linejoin="round"/></svg>
        Resolve PC slowness issues, security vulnerabilities<br>and improper configurations
      </li>
      <li class="benefit">
        <svg class="benefit-tick" viewBox="0 0 20 18" aria-hidden="true"><path d="M2 10 L8 15 L18 2" fill="none" stroke="#e0282f" stroke-width="3" stroke-linecap="round" stroke-linejoin="round"/></svg>
        Validate your backups are working and recoverable in<br>a timely fashion.
      </li>
    </ul>

    <div class="device-visual" role="img" aria-label="Glowing laptop with floating security and user icons"></div>

    <a class="cta-button" href="#book">
      <span class="cta-main">Book An</span>
      <span class="cta-sub">Appointment Now!</span>
    </a>
  </section>
</div>
</body>
</html>
```